Acupuncture business needs business card design

I need a business card for an acupuncture clinic called "Harbourlight Wellness"
It will need the following details:
My name: Marcus Pelling
Acupuncturist
Member TVBH
KWF Treatment Provider
Ph numbers: 581 2734 027 418 5620
Email: marcus@hbwel.example.nz
On the back it will need a table with 2 columns for appointments, one column for time and one for date.

Industry/Entity Type

Clinic

Contact Information for Business Card

Marcus Pelling
Acupuncturist
Member TVBH
KWF Treatment Provider
Email: marcus@hbwel.example.nz

Requirements
Must have
• Marcus Pelling
• Acupuncturist
• Member TVBH
• KWF Treatment Provider
• Ph numbers: 581 2734 027 418 5620
• Email: marcus@hbwel.example.nz
• On the back it will need a table with 2 columns for appointments, one column for time and one for date.

```html
<!DOCTYPE html>
<html lang="en">
<head>
<meta charset="utf-8">
<title>Harbourlight Wellness – Business Card</title>
<link rel="stylesheet" href="https://fonts.googleapis.com/css2?family=Questrial&family=Open+Sans:wght@400;600;700&display=swap">
<style>
  :root{
    --backdrop:#e9e4d6;
    --ink-black:#0b0b0c;
    --brand-cyan:#1aa8d4;
    --band-cyan:#2fb6de;
    --band-teal:#127e98;
    --paper:#ffffff;
    --text-grey:#4a4f55;
    --field-white:#ffffff;
  }
  *{box-sizing:border-box;margin:0;padding:0}
  html,body{width:1200px;height:978px;overflow:hidden}
  body{background:var(--backdrop);position:relative;font-family:"Open Sans",sans-serif}

  .card{position:absolute;width:640px;height:366px;border-radius:22px;overflow:hidden;box-shadow:0 10px 28px rgba(0,0,0,.22)}

  /* Shared brand lockup */
  .brand{display:flex;align-items:center;gap:14px}
  .brand__dot{width:46px;height:46px;border-radius:50%;background:var(--brand-cyan);flex:none}
  .brand__name{font-family:"Questrial",sans-serif;color:var(--brand-cyan);font-size:40px;line-height:1;letter-spacing:.2px;white-space:nowrap}
  .brand__tagline{font-family:"Questrial",sans-serif;color:var(--brand-cyan);font-size:12px;letter-spacing:5.2px;text-transform:uppercase;margin-top:6px;white-space:nowrap}

  /* Back side */
  .card--back{left:230px;top:70px;background:var(--ink-black);color:var(--paper)}
  .card--back .brand{position:absolute;left:54px;top:40px}
  .appointment{position:absolute;left:90px;top:150px;width:470px}
  .appointment__row{display:flex;align-items:center;gap:20px;margin-bottom:18px}
  .appointment__label{width:56px;font-size:21px}
  .appointment__fields{display:flex;gap:8px;flex:1}
  .field{height:30px;background:var(--field-white)}
  .field--time{flex:1}
  .field--day{width:150px}
  .field--month{width:60px}
  .field--year{flex:1}
  .website{position:absolute;left:0;right:0;bottom:42px;text-align:center;font-size:21px;letter-spacing:4px}

  /* Front side */
  .card--front{left:330px;top:520px;background:var(--paper)}
  .card__band{position:absolute;inset:0}
  .card--front .brand{position:absolute;left:36px;top:104px;gap:12px}
  .card--front .brand__dot{width:40px;height:40px}
  .card--front .brand__name{font-size:30px}
  .card--front .brand__tagline{font-size:10px;letter-spacing:3.6px;margin-top:5px}
  .holder{position:absolute;right:26px;top:30px;text-align:right;color:var(--paper);white-space:nowrap}
  .holder__name{font-weight:700;font-size:20px;margin-bottom:3px}
  .holder__role{font-size:12.5px;line-height:1.5}
  .contact{position:absolute;left:42px;top:196px;color:var(--text-grey);font-size:14px}
  .contact__line{display:flex;align-items:center;gap:8px;margin-bottom:10px}
  .contact__icon{width:18px;height:18px;flex:none}
  .address{position:absolute;left:300px;top:250px;padding-left:14px;border-left:1.5px solid var(--text-grey);color:var(--text-grey);font-size:15px;line-height:1.55}
</style>
</head>
<body>

<section class="card card--back" aria-label="Business card, back">
  <div class="brand">
    <span class="brand__dot"></span>
    <div>
      <div class="brand__name">Harbourlight Wellness</div>
      <div class="brand__tagline">Acupuncture Physiotherapy</div>
    </div>
  </div>
  <div class="appointment">
    <div class="appointment__row">
      <span class="appointment__label">Time</span>
      <div class="appointment__fields"><span class="field field--time"></span></div>
    </div>
    <div class="appointment__row">
      <span class="appointment__label">Date</span>
      <div class="appointment__fields">
        <span class="field field--day"></span>
        <span class="field field--month"></span>
        <span class="field field--year"></span>
      </div>
    </div>
  </div>
  <div class="website">www.hbwel.example.nz</div>
</section>

<section class="card card--front" aria-label="Business card, front">
  <svg class="card__band" viewBox="0 0 640 366" width="640" height="366" aria-hidden="true">
    <path d="M370 0 H640 V366 H590 C540 230 470 90 370 0 Z" fill="var(--band-cyan)"/>
    <path d="M370 0 C470 90 540 230 590 366 H563 C515 240 455 100 370 0 Z" fill="var(--band-teal)"/>
    <path d="M370 0 C462 95 528 232 575 366" fill="none" stroke="var(--paper)" stroke-width="3"/>
  </svg>

  <div class="brand">
    <span class="brand__dot"></span>
    <div>
      <div class="brand__name">Harbourlight Wellness</div>
      <div class="brand__tagline">Acupuncture Physiotherapy</div>
    </div>
  </div>

  <div class="holder">
    <div class="holder__name">Marcus Pelling</div>
    <div class="holder__role">Acupuncturist Member TVBH</div>
    <div class="holder__role">KWF Treatment Provider</div>
  </div>

  <div class="contact">
    <div class="contact__line">
      <svg class="contact__icon" viewBox="0 0 18 18" aria-hidden="true"><circle cx="9" cy="9" r="9" fill="var(--brand-cyan)"/><path d="M6 4.5l2 2-1 1.3a6 6 0 0 0 3.2 3.2l1.3-1 2 2-1.4 1.5C8.5 13.4 4.6 9.5 4.5 6z" fill="#fff"/></svg>
      <span>581 2734 &nbsp;027 418 5620</span>
    </div>
    <div class="contact__line">
      <svg class="contact__icon" viewBox="0 0 18 18" aria-hidden="true"><circle cx="9" cy="9" r="9" fill="var(--brand-cyan)"/><rect x="4.5" y="6" width="9" height="6.5" fill="#fff"/><path d="M4.5 6l4.5 3.6L13.5 6" fill="none" stroke="var(--brand-cyan)" stroke-width="1"/></svg>
      <span>marcus@hbwel.example.nz</span>
    </div>
  </div>

  <div class="address">
    <div>Street Name, City Name</div>
    <div>Zipcode-01234</div>
  </div>
</section>

</body>
</html>
```